Interior designer needs a power point template design

I need a template PowerPoint design for my client presentations. The presentations I prepare for my clients usually include the furniture project, the detail of the selected furniture, and the costs. There are a lot of images I insert. What I need is to have a template that I can use for all my presentations, where from time to time I will insert the specific images and descriptions I want to insert. What will always be the same will be the cover, the colors, the font, and the design of the internal sections.
I already have my logo that I would like to insert on each page of the presentation (in small size).
In summary, I need:
- basic template design
- cover with an image chosen by Pictavale photo
- design an internal section/chapter
- internal page design.

I like the clolors of pink and brown <8please see image attached)
Images (will come from Pictavale photo)
● entrance/hall
● living room
● dining room
● Bathroom
● Closet
● Kids room
● Master bedroom
● Master bathroom
● Kitchen
● Office
● Laundry
● Balcony or Terrace

Target Market(s)

Customers (both residential and commercial projects)

Industry/Entity Type

interior design

Font styles to use
Other font styles liked:
• I like courier new

Requirements
Must have
• beautiful design
Should not have
• animations

```html
<!DOCTYPE html>
<html lang="it">
<head>
<meta charset="utf-8">
<title>Casa Lumea – Template presentazione</title>
<link href="https://fonts.googleapis.com/css2?family=Oswald:wght@300;600;700&family=Roboto:wght@400;500;700&display=swap" rel="stylesheet">
<style>
:root{
  --canvas:#a7a9ac;
  --brown:#6e2b0c;
  --pink:#b87868;
  --white:#ffffff;
  --wood-light:#d3c09c;
  --wood-dark:#b59c74;
  --text-light:#f6ece6;
  --muted-pink:#c99383;
}
*{margin:0;padding:0;box-sizing:border-box}
html,body{width:1200px;height:3916px;overflow:hidden}
body{background:var(--canvas);position:relative;font-family:'Roboto',sans-serif}
.slide{position:absolute;width:981px;height:552px;overflow:hidden;box-shadow:0 2px 6px rgba(0,0,0,.25)}
.slide__bg{position:absolute;inset:0;width:100%;height:100%}
.slide--brown{background:var(--pink)}
.slide--light{background:var(--white)}

/* cover */
.cover{background:linear-gradient(100deg,var(--wood-light),var(--wood-dark) 60%,var(--wood-light))}
.cover__art{position:absolute;right:0;top:0;width:560px;height:552px;background:linear-gradient(160deg,rgba(120,80,60,.25),rgba(90,55,40,.45))}
.cover__circle{position:absolute;left:61px;top:71px;width:420px;height:420px;border-radius:50%;background:var(--white);text-align:center}
.brandmark{font-family:'Oswald',sans-serif;font-weight:300;letter-spacing:3px;color:#555;line-height:1}
.cover .brandmark{margin-top:96px;font-size:28px}
.brandmark small{display:block;font-size:9px;letter-spacing:4px;margin-top:4px}
.cover__title{font-family:'Oswald',sans-serif;font-weight:700;font-size:50px;color:var(--brown);margin-top:48px;letter-spacing:.5px}
.cover__tagline{font-weight:700;font-size:13px;color:var(--pink);line-height:19px;margin:14px auto 0;width:300px;text-transform:uppercase}

/* internal */
.slide__logo{position:absolute;top:14px;width:120px;text-align:center}
.slide__logo .brandmark{font-size:20px}
.slide--brown .brandmark{color:var(--text-light)}
.slide--light .brandmark{color:var(--text-light)}
.slide__title{position:absolute;top:36px;font-family:'Oswald',sans-serif;font-weight:700;font-size:36px;letter-spacing:.5px}
.slide--brown .slide__title{color:var(--white);left:301px}
.slide--light .slide__title{color:var(--brown);left:60px}
.slide__photo{position:absolute;top:116px;width:520px;height:390px;border-radius:0 60px 0 60px}
.slide--brown .slide__photo{left:61px}
.slide--light .slide__photo{left:400px}
.slide__copy{position:absolute;top:206px;width:330px}
.slide--brown .slide__copy{left:634px;color:var(--white)}
.slide--light .slide__copy{left:60px;color:var(--brown)}
.slide__subtitle{font-weight:500;font-size:25px;line-height:33px;text-transform:uppercase;margin-bottom:22px}
.slide__text{font-size:11.5px;line-height:19px;margin-bottom:12px}
.slide--light .slide__text{color:#444}

/* contact */
.contact__name{font-weight:700;font-size:28px;color:var(--white);margin-bottom:32px}
.contact__presenter{font-weight:700;font-size:22px;color:var(--muted-pink);margin-bottom:22px}
.contact__row{display:flex;align-items:flex-start;gap:20px;font-weight:700;font-size:14px;color:var(--white);height:41px}
.contact__row svg{flex:none;width:28px;height:28px;margin-top:-6px}
</style>
</head>
<body>

<!-- Cover -->
<section class="slide cover" style="left:114px;top:111px">
  <div class="cover__art" role="img" aria-label="Illustrazione di copertina: rami fioriti e figura con borsa su fondo legno"></div>
  <div class="cover__circle">
    <div class="brandmark">CASA LUMEA<small>INTERIOR DESIGN</small></div>
    <h1 class="cover__title">CASA LUMEA</h1>
    <p class="cover__tagline">Lorem ipsum dolor sit amet, consectetur adipiscing elit</p>
  </div>
</section>

<!-- Camera patronale -->
<section class="slide slide--brown" style="left:114px;top:741px">
  <svg class="slide__bg" viewBox="0 0 981 552"><path d="M320 0H981V552H260Q236 552 236 520V90Q236 0 320 0Z" fill="var(--brown)" stroke="var(--white)" stroke-width="5"/></svg>
  <h2 class="slide__title">CAMERA PATRONALE</h2>
  <div class="slide__logo" style="left:848px"><div class="brandmark">CASA LUMEA<small>INTERIOR</small></div></div>
  <div class="slide__photo" style="background:linear-gradient(180deg,#5d6670,#3a3f46 60%,#8a5a34)" role="img" aria-label="Render della camera patronale con carta da parati floreale e letto"></div>
  <div class="slide__copy">
    <h3 class="slide__subtitle">L'arratmento della camera patronaless</h3>
    <p class="slide__text">Sed ut perspiciatis unde omnis iste natus sit voluptatem accusantium doloremque laudantium, totamaperiam, eaque ipsa quae ab illo inventore veritatis et architecto beatae vitae dicta sunt explicabo.</p>
    <p class="slide__text">Sed ut perspiciatis unde omnis iste natus sit voluptatem accusantium beatae vitae dicta sunt explicabo.</p>
  </div>
</section>

<!-- Cabina armadio -->
<section class="slide slide--light" style="left:114px;top:1369px">
  <svg class="slide__bg" viewBox="0 0 981 552"><path d="M700 0H981V552H776V110Q776 0 700 0Z" fill="var(--pink)" stroke="var(--brown)" stroke-width="4"/></svg>
  <h2 class="slide__title">CABINA ARMADIO</h2>
  <div class="slide__logo" style="left:853px"><div class="brandmark">CASA LUMEA<small>INTERIOR</small></div></div>
  <div class="slide__photo" style="background:linear-gradient(180deg,#e8e8e8,#3b3b40 40%,#5a5a60 75%,#eeeeee)" role="img" aria-label="Render della cabina armadio con abiti appesi e scarpiera"></div>
  <div class="slide__copy">
    <h3 class="slide__subtitle">In 'arrmentmento della sabina armedive</h3>
    <p class="slide__text">Sed ut perspiciatis unde omnis iste natus sit voluptatem accusantium doloremque laudantium, totamaperiam, eaque ipsa quae ab illo inventore veritatis et architecto beatae vitae dicta sunt explicabo.</p>
    <p class="slide__text">Sed ut perspiciatis unde omnis iste natus sit voluptatem accusantium beatae vitae dicta sunt explicabo.</p>
  </div>
</section>

<!-- Bagno patronale -->
<section class="slide slide--brown" style="left:105px;top:1997px">
  <svg class="slide__bg" viewBox="0 0 981 552"><path d="M320 0H981V552H260Q236 552 236 520V90Q236 0 320 0Z" fill="var(--brown)" stroke="var(--white)" stroke-width="5"/></svg>
  <h2 class="slide__title">BY PICNO PATRONALE</h2>
  <div class="slide__logo" style="left:848px"><div class="brandmark">CASA LUMEA<small>INTERIOR</small></div></div>
  <div class="slide__photo" style="background:linear-gradient(180deg,#2e3035,#4a4c52 35%,#c9c9c9 70%,#6d7a6c)" role="img" aria-label="Render del bagno patronale con vasca freestanding e lavabo"></div>
  <div class="slide__copy">
    <h3 class="slide__subtitle">L' arratmento by dela picno patronale</h3>
    <p class="slide__text">Sed ut perspiciatis unde omnis iste natus sit voluptatem accusantium doloremque laudantium, totamaperiam, eaque ipsa quae ab illo inventore veritatis et architecto beatae vitae dicta sunt explicabo.</p>
    <p class="slide__text">Sed ut perspiciatis unde omnis iste natus sit voluptatem accusantium beatae vitae dicta sunt explicabo.</p>
  </div>
</section>

<!-- Dining room -->
<section class="slide slide--light" style="left:114px;top:2625px">
  <svg class="slide__bg" viewBox="0 0 981 552"><path d="M700 0H981V552H776V110Q776 0 700 0Z" fill="var(--pink)" stroke="var(--brown)" stroke-width="4"/></svg>
  <h2 class="slide__title">DINING ROOM</h2>
  <div class="slide__logo" style="left:853px"><div class="brandmark">CASA LUMEA<small>INTERIOR</small></div></div>
  <div class="slide__photo" style="background:linear-gradient(180deg,#eadcd8,#e8705a 40%,#d9d3cf 65%,#7d7f82)" role="img" aria-label="Illustrazione di una sala da pranzo con tavola apparecchiata"></div>
  <div class="slide__copy">
    <h3 class="slide__subtitle">In 'arrmentmento della sabina armedive</h3>
    <p class="slide__text">Sed ut perspiciatis unde omnis iste natus sit voluptatem accusantium doloremque laudantium, totamaperiam, eaque ipsa quae ab illo inventore veritatis et architecto beatae vitae dicta sunt explicabo.</p>
    <p class="slide__text">Sed ut perspiciatis unde omnis iste natus sit voluptatem accusantium beatae vitae dicta sunt explicabo.</p>
  </div>
</section>

<!-- Contact -->
<section class="slide slide--brown" style="left:110px;top:3255px">
  <svg class="slide__bg" viewBox="0 0 981 552"><path d="M320 0H981V552H260Q236 552 236 520V90Q236 0 320 0Z" fill="var(--brown)" stroke="var(--white)" stroke-width="5"/></svg>
  <h2 class="slide__title">CONTACT US</h2>
  <div class="slide__logo" style="left:848px"><div class="brandmark">CASA LUMEA<small>INTERIOR</small></div></div>
  <div class="slide__photo" style="background:linear-gradient(180deg,#2e3035,#d8dadc 30%,#8d8f92 60%,#e7e7e7)" role="img" aria-label="Render di bagno con vasca su piedini e finestra"></div>
  <div class="slide__copy" style="top:172px">
    <h3 class="contact__name">CASA LUMEA</h3>
    <p class="contact__presenter">Presenter Name</p>
    <div class="contact__row">
      <svg viewBox="0 0 24 24" fill="none" stroke="var(--muted-pink)" stroke-width="2"><path d="M5 3h4l2 5-3 2a11 11 0 0 0 6 6l2-3 5 2v4a2 2 0 0 1-2 2A17 17 0 0 1 3 5a2 2 0 0 1 2-2z"/></svg>
      <span>345/8812064</span></div>
    <div class="contact__row">
      <svg viewBox="0 0 24 24" fill="none" stroke="var(--muted-pink)" stroke-width="2"><circle cx="12" cy="12" r="9"/><path d="M3 12h18M12 3c3 3 3 15 0 18M12 3c-3 3-3 15 0 18"/></svg>
      <span>www.CasaLumea.com</span></div>
    <div class="contact__row">
      <svg viewBox="0 0 24 24" fill="none" stroke="var(--muted-pink)" stroke-width="2"><rect x="3" y="5" width="18" height="14"/><path d="M3 5l9 8 9-8"/></svg>
      <span>martaveloni@mailbox.com</span></div>
    <div class="contact__row">
      <svg viewBox="0 0 24 24" fill="none" stroke="var(--muted-pink)" stroke-width="2"><path d="M12 22s7-7 7-12a7 7 0 0 0-14 0c0 5 7 12 7 12z"/><circle cx="12" cy="10" r="2.5"/></svg>
      <span>di Marta Veloni<br>via dei Tigli, 42</span></div>
  </div>
</section>

</body>
</html>
```